TK Homes - Stone Dorf Design

Looking for a double sides design, 1 side for my realestate and the other for home building. ( TK Homes on 1 side, Stone Dorf card on the other Side
Side 1 - Marek Tove ~ Vox Realty logo and Company ( the Property quarter )
Marek Tove
Marek@Marektove.example
IG - Marek_Bzq_Realtor
FB - marekt
Cell - 5558130467
3847 61 St Nw

Side 2
Marek Tove
5558130467
IG - Stonedorf_Bzq
Stonedorfdev@mailbox.example

Target Market(s)

Home buyers/ sellers

Industry/Entity Type

Home builders - Realestate

Contact Information for Business Card

Above

Requirements
Must have
• Black OR White background - my information -

```html
<!DOCTYPE html>
<html lang="en">
<head>
<meta charset="utf-8">
<title>Marek Tove – Business Cards</title>
<link rel="stylesheet" href="https://fonts.googleapis.com/css2?family=Tinos:wght@400;700&display=swap">
<style>
  :root {
    --page: #2a2a2c;
    --card: #1c1c1e;
    --blue: #1a72c4;
    --gold: #f3c22f;
    --white: #f1f1f1;
  }
  * { box-sizing: border-box; margin: 0; padding: 0; }
  html, body { width: 1200px; height: 780px; overflow: hidden; }
  body {
    background: var(--page);
    font-family: "Tinos", "Times New Roman", serif;
    position: relative;
  }
  .card {
    position: absolute;
    top: 235px;
    width: 540px;
    height: 310px;
    background: var(--card);
    overflow: hidden;
    box-shadow: 0 10px 24px rgba(0,0,0,.45);
  }
  .card--realty { left: 40px; }
  .card--builder { left: 620px; }

  .card__divider { position: absolute; inset: 0; width: 540px; height: 310px; }

  .brand {
    position: absolute;
    left: 34px;
    top: 30px;
    font-size: 40px;
    font-weight: 400;
    color: var(--blue);
    letter-spacing: 1px;
    line-height: 1;
  }

  .contacts {
    position: absolute;
    left: 34px;
    top: 178px;
    list-style: none;
  }
  .contacts li {
    display: flex;
    align-items: center;
    gap: 7px;
    font-size: 13.5px;
    line-height: 19px;
    color: var(--white);
  }
  .contacts svg { width: 11px; height: 11px; flex: none; }
  .icon-dot { width: 10px; height: 10px; border-radius: 50%; background: var(--blue); flex: none; }

  .holder {
    position: absolute;
    right: 44px;
    top: 146px;
    text-align: right;
    font-weight: 700;
    line-height: 1;
  }
  .holder__name { font-size: 30px; }
  .holder__first { color: var(--blue); }
  .holder__last { color: var(--gold); }
  .holder__role { display: block; margin-top: 3px; font-size: 17px; color: var(--white); }

  .address {
    position: absolute;
    right: 90px;
    bottom: 14px;
    font-size: 17px;
    line-height: 1;
    color: var(--white);
  }

  .edge-steps { position: absolute; right: 0; top: 200px; width: 22px; }
  .edge-steps span { display: block; height: 16px; background: var(--blue); margin-bottom: 3px; }
  .edge-steps span:nth-child(1) { width: 14px; margin-left: 8px; }
  .edge-steps span:nth-child(2) { width: 22px; }
  .edge-steps span:nth-child(3) { width: 18px; margin-left: 4px; }
  .edge-steps span:nth-child(4) { width: 22px; }
</style>
</head>
<body>

  <section class="card card--realty" aria-label="Realty side">
    <svg class="card__divider" viewBox="0 0 540 310" aria-hidden="true">
      <line x1="34" y1="90" x2="496" y2="262" stroke="#f1f1f1" stroke-width="1.2"/>
    </svg>
    <div class="brand">Marek Tove</div>
    <ul class="contacts">
      <li>
        <svg viewBox="0 0 24 24"><path fill="#1a72c4" d="M6.6 10.8a15 15 0 0 0 6.6 6.6l2.2-2.2a1 1 0 0 1 1-.25 11.4 11.4 0 0 0 3.6.57 1 1 0 0 1 1 1V20a1 1 0 0 1-1 1A17 17 0 0 1 3 4a1 1 0 0 1 1-1h3.5a1 1 0 0 1 1 1c0 1.25.2 2.45.57 3.6a1 1 0 0 1-.25 1z"/></svg>
        5558130467
      </li>
      <li><span class="icon-dot"></span>marekt</li>
      <li><span class="icon-dot"></span>Marek_Bzq_Realtor</li>
      <li>
        <svg viewBox="0 0 24 24"><rect x="2" y="5" width="20" height="14" fill="#1a72c4"/><path d="M2 5l10 8 10-8" fill="none" stroke="#1c1c1e" stroke-width="2"/></svg>
        Marek@Marektove.example
      </li>
      <li>
        <svg viewBox="0 0 24 24"><g fill="none" stroke="#1a72c4" stroke-width="2"><circle cx="12" cy="12" r="10"/><ellipse cx="12" cy="12" rx="4.5" ry="10"/><line x1="2" y1="12" x2="22" y2="12"/></g></svg>
        www.marektove.example
      </li>
    </ul>
    <div class="holder">
      <div class="holder__name"><span class="holder__first">Marek</span> <span class="holder__last">Tove</span></div>
      <span class="holder__role">Director</span>
    </div>
    <div class="edge-steps" aria-hidden="true"><span></span><span></span><span></span><span></span></div>
    <div class="address">3847 61 St Nw</div>
  </section>

  <section class="card card--builder" aria-label="Home building side">
    <svg class="card__divider" viewBox="0 0 540 310" aria-hidden="true">
      <line x1="34" y1="90" x2="496" y2="262" stroke="#f1f1f1" stroke-width="1.2"/>
    </svg>
    <div class="brand">Stone Dorf</div>
    <ul class="contacts">
      <li>
        <svg viewBox="0 0 24 24"><path fill="#1a72c4" d="M6.6 10.8a15 15 0 0 0 6.6 6.6l2.2-2.2a1 1 0 0 1 1-.25 11.4 11.4 0 0 0 3.6.57 1 1 0 0 1 1 1V20a1 1 0 0 1-1 1A17 17 0 0 1 3 4a1 1 0 0 1 1-1h3.5a1 1 0 0 1 1 1c0 1.25.2 2.45.57 3.6a1 1 0 0 1-.25 1z"/></svg>
        5558130467
      </li>
      <li><span class="icon-dot"></span>Stonedorf_Bzq</li>
      <li>
        <svg viewBox="0 0 24 24"><rect x="2" y="5" width="20" height="14" fill="#1a72c4"/><path d="M2 5l10 8 10-8" fill="none" stroke="#1c1c1e" stroke-width="2"/></svg>
        Stonedorfdev@mailbox.example
      </li>
    </ul>
    <div class="holder">
      <div class="holder__name"><span class="holder__first">Marek</span> <span class="holder__last">Tove</span></div>
      <span class="holder__role">Director</span>
    </div>
    <div class="edge-steps" aria-hidden="true"><span></span><span></span><span></span><span></span></div>
  </section>

</body>
</html>
```